Label for Sugar Scrub, sugar peeling

We need a label for a SugarScrub can. We produce both sugar and salt scrubs for B2C and B2B. The market is more dominated by women, but we also want to bring the men on board. In addition to the logo as a font may also fit a picture, a silhouette o.ä. be introduced. Overall, it should be structured rather clearly, more masculine than too flowery and simply modern. It may be multicolored, but not too colorful. The high quality should be highlighted by the design, as it is more in the upper price segment settled. Since we work only with natural "100% Organic" ingredients, it may also be colored accordingly. There will be different fragrances. As an example files, I would attach rosemary lemon. But it should also be a variety of compositions austere nature, other fruits such as grapefruit, lime, etc. are produced. The dimensions of the product label are 25 x 250 mm (WxH). A round logo for the lid is to be designed with 78mm diameter matching, but only logo, the image of the scent direction and the fragrance name or the words "Sugar Scrub" included. As a box will serve, inter alia, a bamboo can, but also a semi-transparent plastic can be used. The sale takes place both online, as in beauty salons and hotels as a product in the exhibition. The label is white or transparent for the plastic box, but only transparent for the bamboo box. In the course I can gladly send the company logo by e-mail. At first I do not want to give away too much. The sample texts for the label are included in the appendix. All in all, however, I would like to give free rein to the freedom of design and not limit too much. Questions can be asked at any time, I will try to answer as soon as possible. However, the project should be open until 16.04. reasonably stand. Otherwise, I can probably only from 18.04. reply.

Target Market(s)

Target market are end users, B2B customers (sauna operators, hotels) and customers of beauty salons.

Font styles to use
Sans Serif

Requirements
Must have
• The three blocks "Ingredients, Logo, Application Recommendation" must be clearly arranged. My logo has the colors (RGB): 63, 148,167 4, 4, 4 152, 152, 152
Nice to have
• It would be nice if it has a rather clear design that appeals to men as well. Possibly. Maybe just by a different color choice could be minted on women.
Should not have
• Not specified....

```html
<!DOCTYPE html>
<html lang="de">
<head>
<meta charset="utf-8">
<title>Verdalune Zuckerpeeling – Etikett und Deckel</title>
<link rel="stylesheet" href="https://fonts.googleapis.com/css2?family=Fira+Sans+Condensed:wght@500&family=Montserrat:wght@500;600;700&display=swap">
<style>
  :root {
    --brand-teal: rgb(63, 148, 167);
    --brand-teal-dark: #2f7d90;
    --brand-black: rgb(4, 4, 4);
    --brand-grey: rgb(152, 152, 152);
    --board-dark: #272727;
    --board-light: #ffffff;
    --organic-green: #8cc63f;
    --label-white: #ffffff;
    --copy-grey: #8e8e8e;
  }
  * { margin: 0; padding: 0; box-sizing: border-box; }
  html, body { width: 1200px; height: 794px; overflow: hidden; }
  body { position: relative; background: var(--board-dark); font-family: "Montserrat", sans-serif; }

  .board-top {
    position: absolute; left: 0; top: 0; width: 1200px; height: 498px;
    background: linear-gradient(180deg, #eef1f3 0%, #ffffff 22%, #ffffff 100%);
  }
  .board-bottom {
    position: absolute; left: 0; top: 498px; width: 1200px; height: 296px;
    background: var(--board-dark);
  }

  .size-note {
    position: absolute; left: 35px; top: 566px;
    color: #ffffff; font-size: 10px; font-weight: 600;
  }

  /* Lid */
  .lid {
    position: absolute; left: 862px; top: 389px; width: 178px; height: 178px;
    border-radius: 50%;
    background: radial-gradient(circle at 40% 35%, var(--brand-teal) 0%, var(--brand-teal-dark) 100%);
    display: flex; flex-direction: column; align-items: center; justify-content: center;
    color: #ffffff;
  }
  .lid-brand { display: flex; align-items: center; gap: 5px; font-size: 22px; font-weight: 600; }
  .lid-brand .dot { width: 8px; height: 8px; border-radius: 50%; background: #ffffff; }
  .lid-rule { width: 126px; height: 1px; background: #ffffff; margin: 8px 0 4px; }
  .lid-product { font-size: 13px; font-weight: 500; letter-spacing: 0.5px; }
  .lid-underline { width: 126px; height: 1px; background: #ffffff; margin-top: 3px; }

  /* Label strip */
  .label {
    position: absolute; left: 26px; top: 592px; width: 1147px; height: 114px;
    background: var(--label-white);
  }
  .copy {
    position: absolute; font-family: "Fira Sans Condensed", sans-serif; font-weight: 500;
    color: var(--copy-grey); font-size: 10px; line-height: 13.5px;
  }
  .copy p + p { margin-top: 8px; }
  .ingredients { left: 67px; top: 12px; width: 300px; }
  .application { left: 775px; top: 30px; width: 300px; }

  .badge {
    position: absolute; left: 388px; top: 34px; width: 70px; height: 70px;
    border-radius: 50%; background: var(--organic-green);
  }
  .brand {
    position: absolute; left: 496px; top: 16px; display: flex; align-items: center; gap: 5px;
    color: var(--brand-teal); font-size: 22px; font-weight: 600;
  }
  .brand .dot { width: 8px; height: 8px; border-radius: 50%; background: var(--brand-teal); }
  .product-name {
    position: absolute; left: 487px; top: 57px;
    color: var(--brand-black); font-size: 13px; font-weight: 700; letter-spacing: 0.3px;
  }
  .scent-band {
    position: absolute; left: 436px; top: 79px; width: 222px; height: 19px;
    background: var(--brand-teal-dark);
    color: #ffffff; font-size: 9.5px; font-weight: 600; letter-spacing: 1.8px;
    display: flex; align-items: center; justify-content: center;
  }
  .scent-art {
    position: absolute; left: 627px; top: 8px; width: 102px; height: 102px;
    border-radius: 40% 50% 50% 50%;
    background: linear-gradient(135deg, #9fae90 0%, #cfd88a 40%, #f6e25a 70%, #fff3a0 100%);
  }
</style>
</head>
<body>
  <div class="board-top"></div>
  <div class="board-bottom"></div>

  <div class="size-note">25 x 250 mm</div>

  <div class="lid">
    <div class="lid-brand"><span>Verdalune</span><span class="dot"></span></div>
    <div class="lid-rule"></div>
    <div class="lid-product">ZUCKERPEELING</div>
    <div class="lid-underline"></div>
  </div>

  <section class="label">
    <div class="copy ingredients">
      <p>Zutaten: Lorem ipsum dolor sit amet, consetetur sadipscing elitr, sed diam nonumy eirmod<br>tempor invidunt ut labore et dolore magna aliquyam erat</p>
      <p>360 gr Netto<br>MHD: 12/2019<br>Recycling Zeichen, Kunststoffbezeichnung</p>
    </div>

    <div class="badge" role="img" aria-label="Bio-Siegel"></div>
    <div class="scent-art" role="img" aria-label="Rosmarinzweig und Zitronenscheibe"></div>
    <div class="brand"><span>Verdalune</span><span class="dot"></span></div>
    <div class="product-name">ZUCKERPEELING</div>
    <div class="scent-band">ROSMARIN-ZITRONE</div>

    <div class="copy application">
      <p>Anwendungshinweis: Nach dem Duschen oder der Sauna anwenden. Haut von überschüssigem Wasser befreien und Peeling kreisend auf die noch feuchte Haut kreisend einmassieren, bis es sich aufgelöst hat. Warm abduschen und Haut mit Handtuch trocken tupfen.</p>
    </div>
  </section>
</body>
</html>
```